Creative, fresh business card design for Ripplecraft Facades

We need a fresh, creative business card design for Ripplecraft Facades. We are the manufacturer of Ripplecraft Facades in Australia. Wall panels are 2400 x 1200mm panels made from MDF and feature 3D patterns on the face of the panel. The colours to be used are green, silver/grey and white RGB
Red 187
Green 207
Blue 65.

An idea is to possibly use a watermark of one of our designs as a background (like on the "Grids" design on the left hand side of page 2 of our brochure).

Target Market(s)

Interior designers, architects, builders and home renovators

Industry/Entity Type

Business

Contact Information for Business Card

Details to go on the card are:
Our logo (attached),
Slogan: "Decorative panels for interiors and exteriors",
Contact name,
Position,
Mobile phone number,
Business address,
Business phone,
Business fax,
Website and
Email address.

I have attached a few images of our panels and our brochure for reference.

The colours of the business card should feature our logo colours which are: RGB
Red 187
Green 207
Blue 65

Requirements
Must have
• Very modern fonts and design. Some of the designs shown especially the "Prisms" design which is a popular design.
Nice to have
• Creative but simple design. Very contemporary.
Should not have
• Anything ornate or old fashioned.

```html
<!DOCTYPE html>
<html lang="en">
<head>
<meta charset="utf-8">
<title>Ripplecraft Facades – Business Card</title>
<link href="https://fonts.googleapis.com/css2?family=Roboto+Condensed:wght@400;700&family=Roboto:wght@300;400;700&display=swap" rel="stylesheet">
<style>
  :root {
    --brand-green: #bbcf41;
    --brand-green-deep: #a8bc30;
    --silver: #9a9b9d;
    --silver-light: #d6d7d9;
    --ink: #1f2410;
    --paper: #ffffff;
    --backdrop: #ecebe7;
    --photo-red: #c23a47;
    --photo-pink: #e06a78;
    --photo-amber: #d99a3a;
  }
  * { box-sizing: border-box; margin: 0; padding: 0; }
  html, body { width: 1200px; height: 950px; overflow: hidden; }
  body {
    background: var(--backdrop);
    font-family: "Roboto", Arial, sans-serif;
    position: relative;
  }
  .card {
    position: absolute;
    left: 220px;
    width: 760px;
    height: 435px;
    background: var(--paper);
    overflow: hidden;
    box-shadow: 0 10px 28px rgba(0,0,0,.18);
  }
  .card--front { top: 30px; }
  .card--back { top: 490px; }

  .card__shapes { position: absolute; inset: 0; width: 100%; height: 100%; }

  /* Brand mark */
  .brand { position: absolute; left: 250px; top: 60px; }
  .brand__row { display: flex; align-items: center; gap: 12px; }
  .brand__square { width: 46px; height: 46px; background: var(--brand-green); }
  .brand__name {
    font-family: "Roboto Condensed", Arial, sans-serif;
    font-weight: 700;
    font-size: 40px;
    color: var(--brand-green-deep);
    letter-spacing: .5px;
  }
  .brand__slogan {
    margin-top: 8px;
    margin-left: 58px;
    font-weight: 300;
    font-size: 17px;
    line-height: 1.15;
    letter-spacing: 2px;
    color: var(--silver);
  }

  /* Person */
  .person {
    position: absolute;
    right: 40px;
    top: 195px;
    text-align: right;
    color: var(--ink);
    font-family: "Roboto Condensed", Arial, sans-serif;
  }
  .person__name { font-weight: 700; font-size: 26px; letter-spacing: .5px; }
  .person__role { font-size: 19px; margin-top: 2px; }
  .person__address { font-size: 19px; line-height: 1.3; margin-top: 4px; }

  /* Contacts */
  .contacts {
    position: absolute;
    left: 40px;
    bottom: 28px;
    list-style: none;
    color: var(--ink);
    font-family: "Roboto Condensed", Arial, sans-serif;
    font-size: 19px;
    line-height: 1.4;
  }
  .contacts__item { display: flex; align-items: center; gap: 10px; }
  .contacts__icon { width: 16px; height: 16px; flex: none; }

  /* Back */
  .back__photo {
    position: absolute; inset: 0;
    background:
      radial-gradient(ellipse at 75% 20%, var(--photo-amber) 0%, transparent 45%),
      linear-gradient(160deg, var(--photo-pink) 0%, var(--photo-red) 55%, #7a2a35 100%);
  }
  .back__brand {
    position: absolute;
    left: 40px; top: 40px;
    display: flex; align-items: center; gap: 12px;
    background: var(--paper);
    padding: 14px 22px;
  }
  .back__brand .brand__name { font-size: 30px; }
  .back__brand .brand__square { width: 34px; height: 34px; }
</style>
</head>
<body>

<section class="card card--front" aria-label="Business card front">
  <svg class="card__shapes" viewBox="0 0 760 435" preserveAspectRatio="none" aria-hidden="true">
    <path d="M0 300 C 220 270, 520 210, 760 60 L760 70 C 520 225, 230 285, 0 318 Z" fill="var(--silver-light)"/>
    <path d="M0 310 C 230 282, 520 220, 760 80 L760 92 C 520 240, 240 298, 0 326 Z" fill="var(--silver)"/>
    <path d="M0 326 C 240 298, 520 240, 760 92 L760 435 L0 435 Z" fill="var(--brand-green)"/>
  </svg>

  <div class="brand">
    <div class="brand__row">
      <span class="brand__square"></span>
      <span class="brand__name">Ripplecraft Facades</span>
    </div>
    <p class="brand__slogan">decorative panels for<br>interiors &amp; landscapes</p>
  </div>

  <div class="person">
    <p class="person__name">AARON WHITLOW</p>
    <p class="person__role">CEO&amp;Founder</p>
    <p class="person__address">42 Harbour Row<br>Geelong, Victoria 3220</p>
  </div>

  <ul class="contacts">
    <li class="contacts__item">
      <svg class="contacts__icon" viewBox="0 0 16 16"><path d="M3 1h3l1 4-2 1a9 9 0 0 0 5 5l1-2 4 1v3a2 2 0 0 1-2 2A13 13 0 0 1 1 3a2 2 0 0 1 2-2z" fill="var(--ink)"/></svg>
      (03) 5521 7480
    </li>
    <li class="contacts__item">
      <svg class="contacts__icon" viewBox="0 0 16 16"><rect x="4" y="1" width="8" height="14" rx="1.5" fill="var(--ink)"/><rect x="5.5" y="3" width="5" height="8" fill="var(--brand-green)"/></svg>
      (03) 5521 7481
    </li>
    <li class="contacts__item">
      <svg class="contacts__icon" viewBox="0 0 16 16"><rect x="1" y="3" width="14" height="10" fill="var(--ink)"/><path d="M1 3l7 6 7-6" stroke="var(--brand-green)" stroke-width="1.4" fill="none"/></svg>
      awhitlow@ripplecraft.com
    </li>
    <li class="contacts__item">
      <svg class="contacts__icon" viewBox="0 0 16 16"><circle cx="8" cy="8" r="7" fill="var(--ink)"/><path d="M1 8h14M8 1c3 3 3 11 0 14M8 1c-3 3-3 11 0 14" stroke="var(--brand-green)" stroke-width="1" fill="none"/></svg>
      www.ripplecraft.com
    </li>
  </ul>
</section>

<section class="card card--back" aria-label="Business card back">
  <div class="back__photo" role="img" aria-label="Photograph of a shop interior lined with red 3D pyramid wall panels, glass shelves and pendant lights"></div>
  <div class="back__brand">
    <span class="brand__square"></span>
    <span class="brand__name">Ripplecraft Facades</span>
  </div>
</section>

</body>
</html>
```